Tree Pruning Website

We need a website for a tree Arborist, pruning company called Maple Crest Canopy Works. We look after all types of trees, knock down trees and prune trees. Our target market is from domestic clients to government clients and everything in between.

We would like to see the use of our main colours which are orange and green

We are not looking forward in seeing a template that we have seen before but a unique template. We have designed 5 templates ourselves and we wish for the design community to take our designs to the next level.

We have also designed a template for things that **we are not** looking for (Version 4)

To make it fair for everyone, we are also not giving out any participation payments as we have had. One winner will take all of the payment!!!

I Have attached a image of the designs and a image of a tree.

We are just looking at the PSD file been developed. We have our own team who can slice the image up into a HTML format.

Target Market(s)

Everyone who needs to cut down a tree

Industry/Entity Type

Government

Requirements
Must have
• Logo on front page
A List of our services
jQuery slider on page
Phone Number on every page

```html
<!DOCTYPE html>
<html lang="en">
<head>
<meta charset="utf-8">
<title>Maple Crest Canopy Works</title>
<link rel="stylesheet" href="https://fonts.googleapis.com/css2?family=Caladea:wght@400;700&family=Titillium+Web:wght@600;700&family=Barlow+Semi+Condensed:wght@600&display=swap">
<style>
:root{
  --cream:#e5e2d0;
  --green:#6b8a14;
  --green-light:#a7c23a;
  --dark:#231d19;
  --darker:#18120e;
  --panel:#3a342b;
  --nav-text:#f1ead7;
  --body-text:#4f4a40;
  --slate:#3c3c3a;
  --box:#faf6dc;
  --muted:#8a8478;
}
*{margin:0;padding:0;box-sizing:border-box}
html,body{width:1136px;height:1200px;overflow:hidden}
body{position:relative;font-family:"Caladea",Georgia,serif;color:var(--body-text);
  background:linear-gradient(#e5e2d0 0,#e5e2d0 320px,#ffffff 480px,#ffffff 100%)}
.abs{position:absolute}
.topbar{left:0;top:0;width:1136px;height:51px;background:linear-gradient(90deg,#1b1915,#2b2925 20%,#1d1b17 50%,#2b2925 80%,#1b1915)}
.nav{left:168px;top:0;width:800px;height:77px;background:linear-gradient(#141310,#2e2c24);border-bottom:3px solid #5a7a10}
.nav a{position:absolute;top:27px;transform:translateX(-50%);font-weight:700;font-size:13.5px;color:var(--nav-text);text-decoration:none;letter-spacing:.3px}
.nav .sep{position:absolute;top:26px;width:1px;height:20px;background:#4a463c}
.logo{left:169px;top:104px;font-family:"Titillium Web",sans-serif;font-weight:700;line-height:1}
.logo .l1{font-size:32px;color:var(--green);letter-spacing:.5px}
.logo .l2{font-size:26px;color:#4a4a42;margin-top:4px;letter-spacing:.5px}
.phone{left:748px;top:126px;display:flex;align-items:center;gap:9px}
.phone .icon{width:31px;height:31px;background:linear-gradient(#b8d14a,#6d8e16);border-radius:2px;display:flex;align-items:center;justify-content:center}
.phone .num{font-family:"Barlow Semi Condensed",sans-serif;font-weight:600;font-size:30px;color:#2c2e30;letter-spacing:.5px}
.slider{left:168px;top:194px;width:800px;height:312px;background:var(--panel);border:2px solid #f6f2d8}
.slide-photo{position:absolute;left:0;top:0;width:520px;height:308px;background:linear-gradient(160deg,#6c7fa8 0%,#d8d2c2 40%,#5a6a3a 75%,#3e4f6a 100%);border-right:3px solid #e9e4ce}
.slide-body{position:absolute;left:548px;top:24px;width:212px}
.slide-body h2{font-weight:400;font-size:28px;color:#8ea82a;margin-bottom:12px}
.slide-body p{font-size:10px;line-height:19.2px;color:#f0ead6;text-align:justify}
.btn-green{display:inline-block;margin-top:14px;padding:8px 12px;background:linear-gradient(#bcd54a,#7d9e18);color:#2a3206;font-size:10px;border:1px solid #d6e58a}
.dots{display:flex;gap:4px;margin-top:18px}
.dots i{width:9px;height:9px;border-radius:50%;background:#cfcabb}
.dots i.on{background:#6b8a14}
.services{left:168px;top:515px;width:212px;height:284px;background:var(--box);border:1px solid #ece5bd;padding:14px 12px}
.services h3{font-weight:400;font-size:19px;color:var(--green);margin-bottom:13px}
.services li{list-style:none;font-size:12.5px;color:#4e4a40;height:27.2px;display:flex;align-items:center;gap:11px;padding-left:6px}
.services li::before{content:"";width:6px;height:6px;border:1px solid #a8a38c;border-radius:50%}
.welcome{left:400px;top:523px;width:568px}
.welcome h1{font-weight:400;font-size:18.5px;color:var(--green);margin-bottom:16px;letter-spacing:.2px}
.welcome p{font-size:9.8px;line-height:19.2px;text-align:justify;margin-bottom:19px;color:#514b42}
.band{left:0;top:820px;width:1136px;height:290px;background:var(--dark)}
.col{position:absolute;top:832px;width:184px}
.col h4{font-weight:400;font-size:19px;color:#7f9b20;margin-bottom:8px}
.col .photo{height:104px;border:1px solid #cfc7b0}
.col p{font-size:9.8px;line-height:16.8px;color:#ece6d4;text-align:justify;margin-top:11px}
.btn-dark{display:inline-block;margin-top:13px;width:74px;height:28px;line-height:28px;text-align:center;background:#4a433b;color:#f0ead6;font-size:10px}
.footer{left:0;top:1110px;width:1136px;height:90px;background:var(--darker)}
.social-title{left:180px;top:1130px;font-size:12.5px;color:#7d776b}
.social{left:181px;top:1158px;display:flex;gap:10px}
.social span{width:21px;height:21px;border-radius:3px;background:linear-gradient(#8a857c,#55504a)}
.foot-links{right:179px;top:1135px;font-size:10px;color:#8c8679}
.copy{right:227px;top:1160px;font-size:10px;color:#8c8679}
</style>
</head>
<body>
<div class="abs topbar"></div>
<nav class="abs nav">
  <a style="left:69px">HOME</a><span class="sep" style="left:116px"></span>
  <a style="left:173px">ABOUT US</a><span class="sep" style="left:233px"></span>
  <a style="left:305px">OUR SERVICES</a><span class="sep" style="left:382px"></span>
  <a style="left:448px">GET A QUOTE</a><span class="sep" style="left:518px"></span>
  <a style="left:579px">OUR WORK</a><span class="sep" style="left:648px"></span>
  <a style="left:709px">CONTACT US</a>
</nav>

<div class="abs logo"><div class="l1">MAPLE CREST</div><div class="l2">CANOPY WORKS</div></div>
<div class="abs phone">
  <div class="icon"><svg width="16" height="16" viewBox="0 0 24 24"><path fill="#1e2406" d="M6.6 10.8a15 15 0 0 0 6.6 6.6l2.2-2.2c.3-.3.7-.4 1-.2 1.1.4 2.3.6 3.6.6.6 0 1 .4 1 1V20c0 .6-.4 1-1 1A17 17 0 0 1 3 4c0-.6.4-1 1-1h3.5c.6 0 1 .4 1 1 0 1.3.2 2.5.6 3.6.1.3 0 .7-.2 1z"/></svg></div>
  <div class="num">08 5550 1234</div>
</div>

<section class="abs slider">
  <div class="slide-photo" role="img" aria-label="Photo looking up into pale-barked gum tree branches against blue sky"></div>
  <div class="slide-body">
    <h2>Tree Pruning</h2>
    <p>Maecenas in quam eget felis tincidunt rutrum vitae vulputate enim. Phasellus nibh augue, varius a placerat quis, mattis sed lacus. Fusce porttitor lobortis lectus eget pharetra. Aliquam vel felis ac ipsum semper feugiat. Nullam nec turpis et velit ultrices venenatis. Etiam dapibus, nunc eget euismod vehicula, nibh nisi lacinia augue, at commodo odio justo sit amet turpis.</p>
    <span class="btn-green">LEARN MORE</span>
    <div class="dots"><i></i><i></i><i class="on"></i><i></i><i></i></div>
  </div>
</section>

<aside class="abs services">
  <h3>OUR SERVICES</h3>
  <ul>
    <li>DIAGNOSIS</li><li>TREATMENT</li><li>PURNING</li><li>TREE REMOVAL</li>
    <li>STUMP REMOVAL</li><li>CABLING &amp; BRACING</li><li>ARBORIST CONSULTS</li><li>TREE PROTECTION</li>
  </ul>
</aside>

<main class="abs welcome">
  <h1>WELCOME TO MAPLE CREST CANOPY WORKS</h1>
  <p>Vestibulum id sapien lorem. Ut mollis lacus a libero consequat mollis. Donec suscipit facilisis diam, vitae volutpat arcu iaculis vel. Maecenas congue condimentum nulla non iaculis. In in felis at orci molestie sagittis.</p>
  <p>Aenean vel lorem enim, sit amet aliquam erat. Cum sociis natoque penatibus et magnis dis parturient montes, nascetur ridiculus mus. Donec in arcu nec orci malesuada scelerisque dignissim a arcu. Suspendisse laoreet neque et tellus posuere ornare. Curabitur velit arcu, pulvinar eget iaculis sit amet, euismod vitae ligula. Phasellus eu ullamcorper turpis. Vivamus leo nibh, tincidunt eu suscipit eget, ultrices eget neque. Curabitur aliquet condimentum lacus, sit amet lacinia magna mattis at. Nullam eget arcu nibh. Etiam imperdiet turpis vitae justo bibendum vel volutpat mauris semper. Vestibulum luctus, urna ac gravida eleifend, nulla enim tempus enim, sed sodales metus dolor sit amet mauris. Proin quam eros, condimentum eu hendrerit sit amet, tristique dictum velit. Mauris fringilla lobortis accumsan. Donec felis odio, commodo sit amet eleifend in, vestibulum sit amet arcu. Proin vestibulum malesuada tortor cursus commodo. Cras viverra neque eget arcu malesuada volutpat. Vivamus porttitor quam quis sapien scelerisque at porta lacus mollis. Curabitur tempus bibendum porta.</p>
</main>

<div class="abs band"></div>
<div class="col" style="left:168px"><h4>DOMESTIC</h4><div class="photo" role="img" aria-label="Wide green tree canopy under a bright blue sky" style="background:linear-gradient(#3f8fd8,#2f5a2a 60%,#6fa6d8)"></div><p>Moleie lacneanrit maellus porase qus esedasese dusce lertswer lrurtasfeugiat malesuad asravida aturs usecuctu aecenas tristique orci acet rtertas dertas. Uls pharetra ma onec accumsan.</p><span class="btn-dark">Read More</span></div>
<div class="col" style="left:373px"><h4>COMMERCIAL</h4><div class="photo" role="img" aria-label="Broken tree stump on green grass" style="background:linear-gradient(90deg,#6f9a3a,#7a5a3a 45%,#b06a2a 60%,#6f9a3a)"></div><p>Moleie lacneanrit maellus porase qus esedasese dusce lertswer lrurtasfeugiat malesuad asravida aturs usecuctu aecenas tristique orci acet rtertas dertas. Uls pharetra ma onec accumsan.</p><span class="btn-dark">Read More</span></div>
<div class="col" style="left:578px"><h4>GOVERNMENT</h4><div class="photo" role="img" aria-label="Autumn trees lining a public street" style="background:linear-gradient(#9a8a2a,#6a6a22 55%,#4a3a2a)"></div><p>Moleie lacneanrit maellus porase qus esedasese dusce lertswer lrurtasfeugiat malesuad asravida aturs usecuctu aecenas tristique orci acet rtertas dertas. Uls pharetra ma onec accumsan.</p><span class="btn-dark">Read More</span></div>
<div class="col" style="left:782px"><h4>NON-PROFIT</h4><div class="photo" role="img" aria-label="Pale branch among green eucalyptus leaves" style="background:linear-gradient(135deg,#4a6a22,#8aa24a 50%,#3a5a1a)"></div><p>Moleie lacneanrit maellus porase qus esedasese dusce lertswer lrurtasfeugiat malesuad asravida aturs usecuctu aecenas tristique orci acet rtertas dertas. Uls pharetra ma onec accumsan.</p><span class="btn-dark">Read More</span></div>

<footer class="abs footer"></footer>
<div class="abs social-title">Find us On Social Networks</div>
<div class="abs social"><span></span><span></span><span></span><span></span><span></span></div>
<div class="abs foot-links">Home | About Us | Our Services | Get a Quote | Our Works | Contact Us</div>
<div class="abs copy">Copyright © 2013, MCCW, All Rights Reserved &nbsp;|&nbsp; Privacy Policy</div>
</body>
</html>
```